German Headhunter/ HR Consultancy needs Business Cards Design

We need a business Card Design for our Company in Stuttgart. We are specialized as Headhunter/ HR Consultancy in Placement of specialist and managers in permanent employment. Please refer to our business logo.

```html
<!DOCTYPE html>
<html lang="en">
<head>
<meta charset="utf-8">
<title>Kernwerk Personalberatung – Business Cards</title>
<link href="https://fonts.googleapis.com/css2?family=Montserrat:wght@600&family=Arimo:wght@400&display=swap" rel="stylesheet">
<style>
  :root {
    --bg: #0e0e10;
    --card: #25262a;
    --card-edge: #3350c4;
    --brand-blue: #3d5ccf;
    --text-grey: #a3a4a8;
    --rule: #4a4b50;
  }
  * { box-sizing: border-box; margin: 0; padding: 0; }
  html, body { width: 1200px; height: 820px; overflow: hidden; }
  body {
    background: var(--bg);
    font-family: "Arimo", Arial, sans-serif;
    position: relative;
  }
  .card {
    position: absolute;
    top: 255px;
    width: 540px;
    height: 310px;
    background: var(--card);
    border-left: 3px solid var(--card-edge);
    border-bottom: 3px solid var(--card-edge);
  }
  .card--front { left: 40px; }
  .card--back { left: 620px; }

  .brand {
    position: absolute;
    display: flex;
    align-items: center;
    gap: 12px;
    color: var(--brand-blue);
    font-family: "Montserrat", Arial, sans-serif;
    font-weight: 600;
    line-height: 1.05;
  }
  .brand__square {
    width: 34px; height: 34px;
    background: var(--brand-blue);
    flex: none;
  }
  .brand__name { font-size: 30px; letter-spacing: 1px; display: block; }
  .brand__tagline { font-size: 12.5px; letter-spacing: 1.2px; display: block; }

  .card--front .brand { top: 46px; left: 200px; }
  .card--back .brand { top: 120px; right: 44px; }

  .rule {
    position: absolute;
    height: 1px;
    background: var(--rule);
  }
  .rule--main { left: 40px; right: 40px; top: 140px; }
  .rule--short { left: 40px; width: 170px; top: 216px; }

  .person { position: absolute; left: 40px; top: 164px; }
  .person__name {
    font-family: "Montserrat", Arial, sans-serif;
    font-weight: 600;
    font-size: 22px;
    color: var(--brand-blue);
    letter-spacing: 0.5px;
  }
  .person__role { font-size: 14px; color: var(--text-grey); margin-top: 2px; }

  .contacts { position: absolute; left: 40px; top: 228px; list-style: none; }
  .contacts li {
    display: flex; align-items: center; gap: 8px;
    font-size: 13.5px; color: var(--text-grey); line-height: 21px;
  }
  .contacts svg { width: 13px; height: 13px; flex: none; }
  .contacts .accent { color: var(--brand-blue); }

  .address {
    position: absolute; right: 40px; top: 164px;
    text-align: right; font-size: 13.5px; color: var(--text-grey); line-height: 20px;
  }
</style>
</head>
<body>
  <section class="card card--front" aria-label="Business card front">
    <div class="brand">
      <span class="brand__square"></span>
      <span>
        <span class="brand__name">KERNWERK</span>
        <span class="brand__tagline">PERSONALBERATUNG</span>
      </span>
    </div>

    <div class="rule rule--main"></div>

    <div class="person">
      <p class="person__name">LUKAS BRENNER</p>
      <p class="person__role">Managing Director</p>
    </div>

    <div class="rule rule--short"></div>

    <ul class="contacts">
      <li>
        <svg viewBox="0 0 16 16" aria-hidden="true"><path d="M4 1.5 6.5 4 5 6c.8 2 2.5 3.8 5 5l2-1.5 2.5 2.5-2 2C7 13.5 2.5 9 2 3.5z" fill="none" stroke="#3d5ccf" stroke-width="1.5"/></svg>
        0711-482 903 17
      </li>
      <li>
        <svg viewBox="0 0 16 16" aria-hidden="true"><rect x="1" y="3" width="14" height="10" fill="#3d5ccf"/><path d="M1 3l7 6 7-6" fill="none" stroke="#25262a" stroke-width="1.3"/></svg>
        kontakt@kernwerk-hr.de
      </li>
      <li>
        <svg viewBox="0 0 16 16" aria-hidden="true"><circle cx="8" cy="8" r="6.5" fill="none" stroke="#3d5ccf" stroke-width="1.4"/><ellipse cx="8" cy="8" rx="2.8" ry="6.5" fill="none" stroke="#3d5ccf" stroke-width="1.1"/><path d="M1.5 8h13" stroke="#3d5ccf" stroke-width="1.1"/></svg>
        <span>www.<span class="accent">kernwerk-hr</span>.de</span>
      </li>
    </ul>

    <p class="address">Lindenweg 14, 3. Etage<br>70173 Stuttgart, Deutschland</p>
  </section>

  <section class="card card--back" aria-label="Business card back">
    <div class="brand">
      <span class="brand__square"></span>
      <span>
        <span class="brand__name">KERNWERK</span>
        <span class="brand__tagline">PERSONALBERATUNG</span>
      </span>
    </div>
  </section>
</body>
</html>
```